Pet store web design

I would like to redesign my current online store (http://furrowlanemart.com)
I'm looking for a clean, modern design. Any ideas are welcome..

Industry/Entity Type

Pet

Number of Pages Required

3 page

```html
<!DOCTYPE html>
<html lang="en">
<head>
<meta charset="utf-8">
<title>Furrow Lane Mart – Pet Store</title>
<link href="https://fonts.googleapis.com/css2?family=Oswald:wght@400;500;700&family=Open+Sans:wght@400;600;700&display=swap" rel="stylesheet">
<style>
:root{
  --black:#111;
  --dark:#2b2b2b;
  --darker:#1c1c1c;
  --bar:#3a3a3a;
  --yellow:#ffd200;
  --orange:#f39a12;
  --red:#d9261c;
  --teal:#18a6ab;
  --teal-dark:#0d6f73;
  --text:#333;
  --muted:#8a8a8a;
  --light:#f1f1f1;
  --white:#fff;
}
*{box-sizing:border-box;margin:0;padding:0}
html,body{width:1200px;height:2184px;overflow:hidden}
body{position:relative;background:var(--white);font-family:"Open Sans",sans-serif;color:var(--text);font-size:12px}
.section{position:absolute;left:0;width:1200px}
.h{font-family:"Oswald",sans-serif;text-transform:uppercase}

/* top bar */
.topbar{top:0;height:24px;background:var(--black);display:flex;align-items:center;justify-content:space-between;padding:0 40px;font-size:10px;color:var(--yellow)}
.topbar .links span{margin-right:14px}
.topbar .links span.pill{background:var(--yellow);color:var(--black);padding:1px 6px;border-radius:2px}

/* header */
.header{top:24px;height:76px;display:flex;align-items:center;padding:0 40px}
.logo{display:flex;align-items:center;gap:8px;font-family:"Oswald",sans-serif;font-weight:700;font-size:22px;color:var(--orange)}
.logo i{width:16px;height:16px;border-radius:50%;background:var(--orange);display:block}
.nav{display:flex;gap:26px;margin-left:auto;margin-right:40px;font-family:"Oswald",sans-serif;font-size:13px;font-weight:500;color:#5a1e12}
.cart{width:34px;height:34px;border-radius:50%;background:var(--black);display:flex;align-items:center;justify-content:center;margin-right:80px}

/* hero */
.hero{top:100px;height:440px;background:linear-gradient(135deg,#cfe0a8 0%,#8fb05a 45%,#5e7d36 75%,#a9c07a 100%)}
.hero-caption{position:absolute;left:690px;top:240px;width:260px;background:rgba(20,20,20,.72);padding:14px 16px;color:var(--white)}
.hero-caption .h{font-size:20px;font-weight:500}
.hero-caption p{font-size:10px;margin:4px 0 10px}
.btn-yellow{display:inline-block;background:var(--yellow);color:var(--black);font-family:"Oswald",sans-serif;font-size:11px;padding:4px 12px;text-transform:uppercase}
.dots{position:absolute;bottom:14px;left:0;width:100%;display:flex;justify-content:center;gap:6px}
.dots i{width:8px;height:8px;border-radius:50%;background:rgba(255,255,255,.6);display:block}
.dots i:first-child{background:var(--yellow)}

/* categories */
.categories{top:540px;height:256px;background:var(--light);display:flex;gap:10px;padding:10px 40px}
.cat{flex:1;background:var(--white)}
.cat-head{height:42px;color:var(--white);text-align:center;padding-top:5px}
.cat-head .h{font-size:14px;display:block}
.cat-head small{font-size:8px}
.cat-img{height:186px}
.c1{background:var(--teal)}.c2{background:#1b8fc9}.c3{background:var(--red)}.c4{background:#6cb33f}.c5{background:var(--orange)}

/* products */
.products{top:820px;height:250px;padding:0 40px}
.tabs{display:flex;gap:30px;border-bottom:1px solid #ddd;font-family:"Oswald",sans-serif;font-size:11px;color:var(--muted);padding-bottom:8px}
.tabs span:first-child{color:var(--black);border-bottom:2px solid var(--yellow);padding-bottom:7px;margin-bottom:-9px}
.grid{display:flex;gap:20px;margin-top:16px}
.card{flex:1;border:1px solid #eee;padding:8px}
.card .img{height:118px;margin-bottom:8px}
.card .name{font-size:9px;font-weight:600;color:var(--text)}
.card .row{display:flex;justify-content:space-between;align-items:center;margin-top:4px;font-size:10px}
.stars{color:var(--yellow);font-size:10px;letter-spacing:1px}
.price{color:var(--red);font-weight:700}
.btn-red{display:inline-block;background:var(--red);color:var(--white);font-size:8px;font-weight:700;padding:3px 8px;text-transform:uppercase;margin-top:6px}

/* banner */
.banner{top:1092px;height:110px;background:var(--teal);display:flex;align-items:center}
.banner-img{width:220px;height:96px;margin-left:190px;background:radial-gradient(circle at 40% 50%,#e7c992,#b4884f 60%,var(--teal) 62%)}
.banner-text{flex:1;text-align:center;color:var(--white);padding-right:120px}
.banner-text .h{font-size:34px;font-weight:500;letter-spacing:1px}
.banner-text .pill{display:inline-block;background:var(--teal-dark);font-family:"Oswald",sans-serif;font-size:12px;padding:3px 18px;border-radius:12px;margin-top:4px}

/* popular */
.popular{top:1332px;height:268px;padding:0 40px;display:flex;gap:30px}
.popular-box{width:330px;background:var(--yellow);padding:24px 26px;color:var(--black)}
.popular-box .h{font-size:36px;font-weight:700;line-height:1}
.popular-box p{font-size:10px;margin-top:14px;line-height:1.5}
.popular-list{flex:1;display:flex;align-items:center;gap:18px}
.arrow{font-family:"Oswald",sans-serif;font-size:22px;color:#bbb}
.pop{flex:1;text-align:center}
.pop .img{height:150px;margin-bottom:10px}
.pop .name{font-size:9px;color:var(--muted)}
.pop .price{font-size:14px;margin-top:4px}

/* features */
.features{top:1620px;height:84px;display:flex;justify-content:space-around;align-items:center;padding:0 60px;border-top:1px solid #eee}
.feature{display:flex;align-items:center;gap:10px}
.feature .icon{width:40px;height:40px;border-radius:50%;background:var(--yellow);display:flex;align-items:center;justify-content:center}
.feature b{font-size:11px;display:block}
.feature small{font-size:8px;color:var(--muted)}

/* newsletter */
.newsletter{top:1708px;height:52px;background:var(--bar);display:flex;align-items:center;padding:0 40px;gap:16px;color:var(--white);font-size:10px}
.newsletter .input{width:420px;height:24px;background:var(--white);margin-left:auto}
.newsletter .btn-yellow{height:24px;padding:4px 24px}

/* footer */
.footer{top:1760px;height:380px;background:var(--dark);color:#bbb;display:flex;padding:26px 40px;gap:40px;font-size:10px}
.col{flex:1}
.col h4{font-family:"Oswald",sans-serif;font-weight:500;color:var(--white);font-size:13px;text-transform:uppercase;margin-bottom:12px}
.col h4.sub{margin-top:22px}
.col ul{list-style:none}
.col li{margin-bottom:7px;padding-left:12px;position:relative}
.col li::before{content:"";position:absolute;left:0;top:5px;width:5px;height:5px;background:var(--yellow);border-radius:50%}
.footer-logo{display:inline-flex;align-items:center;gap:6px;background:var(--yellow);padding:8px 12px;font-family:"Oswald",sans-serif;font-weight:700;font-size:15px;color:var(--black);margin-bottom:12px}
.footer-logo i{width:10px;height:10px;border-radius:50%;background:var(--black);display:block}
.col p{line-height:1.6}
.cards{display:flex;gap:6px}
.cards span{width:38px;height:24px;background:#ddd;border-radius:3px}
.social{display:flex;gap:6px}
.social span{width:22px;height:22px;border-radius:50%;background:var(--yellow)}
.contact-line{display:flex;gap:8px;margin-bottom:8px;align-items:center}
.copyright{top:2140px;height:44px;background:var(--darker);color:#999;font-size:10px;display:flex;align-items:center;justify-content:center}
</style>
</head>
<body>

<div class="section topbar">
  <div class="links"><span class="pill">My Account</span><span>Wishlist</span><span>Checkout</span><span>Log In</span></div>
  <div class="links"><span>Sign In</span><span>Register</span></div>
</div>

<header class="section header">
  <div class="logo"><i></i>Furrow Lane Mart</div>
  <nav class="nav"><span>DOG ▾</span><span>CAT ▾</span><span>FISH ▾</span><span>BIRD ▾</span><span>SMALL PET ▾</span><span>ABOUT US</span><span>CAREERS</span><span>CONTACT US</span></nav>
  <div class="cart"><svg width="16" height="16" viewBox="0 0 16 16"><path d="M1 2h3l2 8h7l2-6H5" fill="none" stroke="#ffd200" stroke-width="1.6"/><circle cx="7" cy="13" r="1.3" fill="#ffd200"/><circle cx="12" cy="13" r="1.3" fill="#ffd200"/></svg></div>
</header>

<section class="section hero" role="img" aria-label="Photo of a boy and his mother playing with a brown dog on a lawn">
  <div class="hero-caption">
    <div class="h">Grooming Products</div>
    <p>A wide selection of best grooming products from our online store</p>
    <span class="btn-yellow">Shop Now</span>
  </div>
  <div class="dots"><i></i><i></i><i></i></div>
</section>

<section class="section categories">
  <div class="cat"><div class="cat-head c1"><span class="h">Fish / Winter</span><small>Warm coats for cold days</small></div><div class="cat-img" role="img" aria-label="Dog wearing a police vest" style="background:linear-gradient(#3b3b3b,#1c1c1c)"></div></div>
  <div class="cat"><div class="cat-head c2"><span class="h">Fish / Winter</span><small>Keep pets warm and cosy</small></div><div class="cat-img" role="img" aria-label="Dog in a winter jacket" style="background:linear-gradient(#d9d9d9,#8c8c8c)"></div></div>
  <div class="cat"><div class="cat-head c3"><span class="h">Fish / Winter</span><small>Pet carriers on sale now</small></div><div class="cat-img" role="img" aria-label="Red pet carrier trolley" style="background:linear-gradient(#f2f2f2,#c23a30)"></div></div>
  <div class="cat"><div class="cat-head c4"><span class="h">Soft Rubber Toys</span><small>Fun chew toys for dogs</small></div><div class="cat-img" role="img" aria-label="Dog playing with a rubber toy" style="background:linear-gradient(#f0e2c2,#c99a5a)"></div></div>
  <div class="cat"><div class="cat-head c5"><span class="h">Pet Dogs Bed</span><small>Soft beds for every size</small></div><div class="cat-img" role="img" aria-label="Dog resting in a pet bed" style="background:linear-gradient(#e4d8c6,#9c8468)"></div></div>
</section>

<section class="section products">
  <div class="tabs"><span>DOG</span><span>CAT</span><span>FISH</span><span>BIRD</span><span>SMALL PET</span></div>
  <div class="grid">
    <div class="card"><div class="img" role="img" aria-label="Pet food dispenser" style="background:radial-gradient(circle,#e3b23c,#fff 70%)"></div><div class="name">Automatic pet food dispenser, gold</div><div class="row"><span class="stars">★★★★☆</span><span class="price">$24.50</span></div><span class="btn-red">Add to cart</span></div>
    <div class="card"><div class="img" role="img" aria-label="Wooden dog kennel" style="background:radial-gradient(circle,#b0703a,#fff 70%)"></div><div class="name">Wooden outdoor dog kennel, medium</div><div class="row"><span class="stars">★★★★☆</span><span class="price">$89.00</span></div><span class="btn-red">Add to cart</span></div>
    <div class="card"><div class="img" role="img" aria-label="Blue fabric pet carrier" style="background:radial-gradient(circle,#3c7fc4,#fff 70%)"></div><div class="name">Soft fabric pet carrier, blue</div><div class="row"><span class="stars">★★★★☆</span><span class="price">$47.77</span></div><span class="btn-red">Add to cart</span></div>
    <div class="card"><div class="img" role="img" aria-label="Red pet treadmill" style="background:radial-gradient(circle,#d13a2f,#fff 70%)"></div><div class="name">Indoor pet treadmill, red</div><div class="row"><span class="stars">★★★★☆</span><span class="price">$603.85</span></div><span class="btn-red">Add to cart</span></div>
  </div>
</section>

<section class="section banner">
  <div class="banner-img" role="img" aria-label="Group of pet food packs and a puppy"></div>
  <div class="banner-text">
    <div class="h">30 New Pet Products Every Month</div>
    <span class="pill">FREE DELIVERY ON ORDERS OVER $70</span>
  </div>
</section>

<section class="section popular">
  <div class="popular-box">
    <div class="h">Most<br>Popular</div>
    <p>Our best loved picks this season, chosen by pet owners like you. Browse the beds, coats and gear that keep tails wagging, all with fast delivery and easy returns.</p>
  </div>
  <div class="popular-list">
    <span class="arrow">‹</span>
    <div class="pop"><div class="img" role="img" aria-label="Small dog in a knitted sweater" style="background:radial-gradient(circle,#d9d9d9,#fff 70%)"></div><div class="name">Knitted dog sweater, large</div><div class="price">$30.69</div></div>
    <div class="pop"><div class="img" role="img" aria-label="Round green pet bed" style="background:radial-gradient(circle,#8fae5a,#fff 70%)"></div><div class="name">Round plush pet bed, green</div><div class="price">$105.15</div></div>
    <div class="pop"><div class="img" role="img" aria-label="Red pet treadmill" style="background:radial-gradient(circle,#d13a2f,#fff 70%)"></div><div class="name">Indoor pet treadmill, red</div><div class="price">$603.85</div></div>
    <span class="arrow">›</span>
  </div>
</section>

<section class="section features">
  <div class="feature"><div class="icon"><svg width="22" height="16" viewBox="0 0 22 16"><path d="M1 2h12v9H1zM13 5h4l3 3v3h-7z" fill="#111"/><circle cx="5" cy="13" r="2" fill="#111"/><circle cx="16" cy="13" r="2" fill="#111"/></svg></div><div><b>Delivery Information</b><small>Fast shipping nationwide</small></div></div>
  <div class="feature"><div class="icon"><svg width="18" height="18" viewBox="0 0 18 18"><path d="M4 7a6 6 0 1 1 1 6" fill="none" stroke="#111" stroke-width="2"/><path d="M1 4l3 4 4-3z" fill="#111"/></svg></div><div><b>Returns Policy</b><small>Easy thirty day returns</small></div></div>
  <div class="feature"><div class="icon"><svg width="16" height="20" viewBox="0 0 16 20"><path d="M3 6a5 5 0 1 1 7 4c-2 1-2 2-2 4" fill="none" stroke="#111" stroke-width="2.2"/><circle cx="8" cy="18" r="1.5" fill="#111"/></svg></div><div><b>Questions Ask</b><small>We reply within a day</small></div></div>
  <div class="feature"><div class="icon"><svg width="18" height="18" viewBox="0 0 18 18"><path d="M4 1l3 4-2 2c1 2 3 4 6 6l2-2 4 3-2 3C8 17 1 10 1 3z" fill="#111"/></svg></div><div><b>Let us help you</b><small>Call our friendly team</small></div></div>
</section>

<section class="section newsletter">
  <span>Keep up to date with the latest from furrowlanemart.com. We love pets.</span>
  <div class="input"></div>
  <span class="btn-yellow">Subscribe</span>
</section>

<footer class="section footer">
  <div class="col">
    <h4>About Us</h4>
    <div class="footer-logo"><i></i>Furrow Lane Mart</div>
    <p>Welcome to Furrow Lane Mart, your one-stop shop for premium pet supplies. We offer food, beds, toys and care products for dogs, cats, fish, birds and small pets, delivered to your door.</p>
  </div>
  <div class="col">
    <h4>Services</h4>
    <ul><li>Pet Grooming</li><li>Pet Sitting</li><li>Dog Walking</li><li>Pet Hotel</li><li>Puppy School</li></ul>
    <h4 class="sub">Shop Now</h4>
    <ul><li>Dog</li><li>Cat</li><li>Fish</li><li>Bird</li><li>Small Pet</li></ul>
  </div>
  <div class="col">
    <h4>Shopping Online</h4>
    <ul><li>Delivery Information</li><li>Privacy Policy</li><li>Returns Policy</li><li>Terms and Conditions</li><li>FAQs</li></ul>
    <h4 class="sub">We Accept</h4>
    <div class="cards"><span></span><span></span><span></span><span></span></div>
  </div>
  <div class="col">
    <h4>Contact</h4>
    <div class="contact-line"><svg width="10" height="14" viewBox="0 0 10 14"><path d="M5 0a5 5 0 0 1 5 5c0 4-5 9-5 9S0 9 0 5a5 5 0 0 1 5-5z" fill="#ffd200"/></svg>12 Orchard Row, Millbrook</div>
    <div class="contact-line"><svg width="12" height="12" viewBox="0 0 18 18"><path d="M4 1l3 4-2 2c1 2 3 4 6 6l2-2 4 3-2 3C8 17 1 10 1 3z" fill="#ffd200"/></svg>(555) 014-2280</div>
    <div class="contact-line"><svg width="12" height="10" viewBox="0 0 12 10"><rect width="12" height="10" fill="#ffd200"/><path d="M0 0l6 5 6-5" fill="none" stroke="#2b2b2b"/></svg>hello@furrowlanemart.com</div>
    <h4 class="sub">Let's Become Friends</h4>
    <div class="social"><span></span><span></span><span></span><span></span><span></span></div>
  </div>
</footer>

<div class="section copyright">© 2015 Furrow Lane Mart. All Rights Reserved</div>

</body>
</html>
```